Website Refresh

I'm looking to refresh my Squarespace website. www.derekmulvane.com

I am pretty happy with the content but would like a better navigation bar, livelier color choices, consistent type faces, and a more modern look. I am willing to pay extra to implement suggested improvements that would make the site more appealing

```html
<!DOCTYPE html>
<html lang="en">
<head>
<meta charset="utf-8">
<title>Derek Mulvane – Summitry Peer Group</title>
<link href="https://fonts.googleapis.com/css2?family=Montserrat:ital,wght@0,400;0,500;0,600;0,700;0,800;0,900;1,400&display=swap" rel="stylesheet">
<style>
:root{
  --navy:#0f2c4c;
  --black:#111418;
  --sky:#48b3f7;
  --sky-text:#4bb6fb;
  --text:#333a44;
  --muted:#5c6470;
  --white:#ffffff;
}
*{box-sizing:border-box;margin:0;padding:0}
html,body{width:1200px;height:3423px;overflow:hidden}
body{font-family:'Montserrat',sans-serif;color:var(--text);background:var(--white);position:relative}
.abs{position:absolute}
.btn{display:inline-block;background:var(--navy);color:var(--white);font-size:12px;font-weight:500;letter-spacing:.3px;text-transform:uppercase;padding:0 18px;line-height:35px;border-radius:2px;white-space:nowrap}

/* header */
.site-header{top:0;left:0;width:1200px;height:87px;background:var(--white)}
.brand{left:112px;top:18px}
.brand-row{display:flex;align-items:center;gap:10px}
.brand-mark{width:18px;height:18px;background:var(--navy)}
.brand-name{font-size:28px;font-weight:600;color:var(--navy);line-height:32px}
.brand-tag{font-size:11px;color:var(--muted);line-height:14px;margin-top:4px}
.contact{left:500px;top:20px;text-align:right;width:316px}
.contact small{display:block;font-size:11px;color:var(--text);letter-spacing:.5px}
.contact b{display:flex;align-items:center;justify-content:flex-end;gap:10px;font-size:17px;font-weight:700;color:var(--navy);margin-top:6px;white-space:nowrap}
.divider{width:3px;height:36px;background:var(--navy);top:24px}
.social-sq{left:858px;top:24px;width:36px;height:36px;border:3px solid var(--navy);border-radius:4px}
.join{left:938px;top:24px;line-height:36px;font-size:12px}

.main-nav{top:87px;left:0;width:1200px;height:46px;background:var(--black);display:flex;align-items:center;padding-left:131px;gap:25px}
.main-nav a{color:#e9ecef;font-size:13.5px;font-weight:500;text-transform:uppercase;text-decoration:none;white-space:nowrap}

/* hero */
.hero{top:133px;left:0;width:1200px;height:594px;background:linear-gradient(180deg,#2a4f78 0%,#23466d 60%,#1c3a5d 100%)}
.hero-copy{top:312px;width:1200px;text-align:center;color:var(--white)}
.hero-copy .eyebrow{font-size:49px;font-weight:400;letter-spacing:1px;line-height:56px}
.hero-copy h1{font-size:74px;font-weight:900;color:var(--sky-text);line-height:84px;letter-spacing:1px}
.hero-copy p{font-size:19px;line-height:33px;margin-top:10px}
.play{left:571px;top:544px;width:58px;height:58px;border:2px solid var(--white)}
.hero-band{top:596px;left:0;width:1200px;height:131px;background:rgba(12,30,52,.35)}

/* invitation box */
.invite{top:663px;left:112px;width:976px;height:218px;background:var(--sky);border-radius:80px 80px 0 0;color:var(--white);text-align:center;padding-top:47px}
.invite h2{font-size:25px;font-weight:500;letter-spacing:.3px}
.invite .row{display:flex;justify-content:center;align-items:center;gap:14px;font-size:22px;margin-top:20px}
.invite .row + .row{margin-top:16px}
.tick{display:inline-flex;align-items:center;gap:12px}

/* intro */
.intro{top:727px;left:0;width:1200px;height:975px;background:linear-gradient(180deg,#eceef1,#f5f6f8 40%,#e9ebef)}
.intro-lines{top:955px;width:1200px;text-align:center;color:var(--navy);font-weight:600;font-size:22px;line-height:29px}
.intro-lines p{margin-bottom:28px}
.awards{top:1207px;left:112px;width:470px}
.awards h3{font-size:17.5px;color:var(--navy);font-weight:600;line-height:24px}
.awards .lead{font-size:12px;color:var(--muted);line-height:19px;margin-top:14px}
.awards ul{list-style:none;margin-top:14px}
.awards li{font-size:12px;color:var(--muted);line-height:19px;margin-bottom:19px;position:relative;padding-left:31px}
.awards li::before{content:"";position:absolute;left:0;top:4px;width:12px;height:12px;border-radius:50%;background:var(--navy)}
.awards li::after{content:"";position:absolute;left:3px;top:8px;width:4px;height:4px;border-right:1.5px solid #fff;border-top:1.5px solid #fff;transform:rotate(45deg)}
.awards li.wrap{padding-left:0;text-indent:31px}
.awards .btn{margin-top:8px}
.photo-frame{left:634px;top:1234px;width:470px;height:372px;border:6px solid var(--navy)}
.photo-meeting{left:616px;top:1216px;width:471px;height:373px;background:linear-gradient(160deg,#8d939b,#4c5560 60%,#2d333b)}

/* testimonials */
.quote-card{left:112px;top:1880px;width:471px;height:368px;background:var(--white);box-shadow:0 4px 18px rgba(0,0,0,.12)}
.portrait{left:141px;top:1811px;width:203px;height:205px;background:linear-gradient(160deg,#7c7a76,#3f3c39)}
.arrows{left:360px;top:1813px;display:flex;gap:10px}
.arrows span{width:26px;height:26px;border-radius:50%;background:var(--navy);display:flex;align-items:center;justify-content:center}
.arrows span + span{background:#7c8a9c}
.quote-mark{left:370px;top:1890px;font-size:50px;font-weight:800;color:var(--navy);line-height:50px}
.quote-who{left:369px;top:1942px;font-size:14.5px;line-height:25px;color:var(--muted)}
.quote-who b{color:var(--navy);font-weight:700;font-size:15.5px}
.quote-rule{left:134px;top:2056px;width:428px;height:1px;background:#cfd3d8}
.quote-body{left:130px;top:2082px;width:436px;text-align:center;font-style:italic;font-size:12.8px;line-height:22px;color:var(--muted)}
.say{left:618px;top:1800px;width:482px}
.say .eyebrow{font-size:25px;color:var(--navy);font-weight:400;line-height:32px}
.say h2{font-size:34px;font-weight:800;color:var(--navy);line-height:46px;white-space:nowrap}
.say p{font-size:15.5px;line-height:26.6px;color:var(--text);margin-top:18px}
.say .name{font-weight:600;color:var(--navy);font-size:15.5px;margin-top:18px}
.say .role{font-size:14px;color:var(--muted);margin-top:4px}
.say .btn{margin-top:26px;font-size:12.5px}

/* blog */
.blog-band{top:2350px;left:0;width:1200px;height:220px;background:var(--navy);border-radius:80px 80px 0 0}
.blog-head{top:2393px;width:1200px;text-align:center;color:var(--white)}
.blog-head .eyebrow{font-size:24px;font-weight:400;line-height:30px}
.blog-head h2{font-size:37px;font-weight:800;line-height:46px;letter-spacing:.3px}
.card{top:2508px;width:314px;height:399px;background:var(--white);box-shadow:0 4px 16px rgba(0,0,0,.1);text-align:center}
.card .thumb{width:314px;height:275px;border-bottom:6px solid var(--navy);position:relative}
.card .date{position:absolute;left:104px;bottom:-6px;width:106px;height:26px;background:var(--navy);color:var(--white);font-size:12px;font-weight:700;line-height:26px}
.card h3{font-size:14px;font-weight:700;color:#222;text-transform:uppercase;line-height:24px;margin-top:32px;padding:0 8px;white-space:nowrap}
.card a{display:inline-block;font-size:12px;color:#333;margin-top:12px;text-decoration:underline}
.more-news{left:498px;top:2937px;width:206px;text-align:center;font-size:12.5px}

/* footer */
.site-footer{top:3077px;left:0;width:1200px;height:346px;background:var(--navy);color:var(--white)}
.f-brand{left:112px;top:3130px;width:226px}
.f-brand .brand-mark{background:var(--white);width:20px;height:20px}
.f-brand .brand-name{color:var(--white);font-size:32px;line-height:36px}
.f-brand .brand-tag{color:#c9d3df;font-size:12.5px;line-height:17px;margin-top:6px}
.f-vline{width:1px;height:118px;background:#5a728e;top:3150px}
.f-col{top:3124px;color:var(--white)}
.f-col h4{font-size:17.5px;font-weight:500;margin-bottom:18px}
.f-col .item{font-size:12.5px;font-weight:600;line-height:19px;margin-bottom:19px;display:flex;gap:6px;white-space:nowrap}
.f-col .link{font-size:12.5px;font-weight:600;line-height:26px;white-space:nowrap}
.f-social{display:flex;gap:12px;margin-top:2px}
.f-social span{width:24px;height:24px;border-radius:50%;background:var(--white)}
.f-social span + span{border-radius:3px}
.f-rule{left:112px;top:3345px;width:976px;height:1px;background:#3f5a79}
.copyright{top:3371px;width:1200px;text-align:center;font-size:12.5px;font-weight:500;color:var(--white)}
.code{left:1150px;top:3369px;font-size:12px;color:var(--white)}
</style>
</head>
<body>

<header class="site-header abs">
  <div class="brand abs">
    <div class="brand-row"><span class="brand-mark"></span><span class="brand-name">Summitry</span></div>
    <div class="brand-tag">Peer councils for company leaders and founders.</div>
  </div>
  <div class="contact abs">
    <small>CONTACT</small>
    <b><svg width="20" height="15" viewBox="0 0 20 15"><rect width="20" height="15" rx="2" fill="#0f2c4c"/><path d="M1 2l9 7 9-7" stroke="#fff" stroke-width="1.6" fill="none"/></svg>Derek @ DerekMulvane.com</b>
  </div>
  <div class="divider abs" style="left:835px"></div>
  <div class="social-sq abs"></div>
  <div class="divider abs" style="left:912px"></div>
  <div class="btn join abs">Join the group</div>
</header>

<nav class="main-nav abs">
  <a>About the group</a><a>Member video testimonials</a><a>Testimonials</a><a>Success stories</a><a>Derek's blog</a><a>Derek Mulvane bio</a>
</nav>

<section class="hero abs" role="img" aria-label="Background video still of a member speaking to camera"></section>
<div class="hero-band abs"></div>
<div class="hero-copy abs">
  <div class="eyebrow">TURNING GOOD CEO’S</div>
  <h1>INTO GREAT CEO’S</h1>
  <p>Our award winning CEOs will help you make better decisions<br>for your company, family, and community .</p>
</div>
<div class="play abs"><svg width="54" height="54" viewBox="0 0 54 54"><path d="M22 18l13 9-13 9z" fill="#fff"/></svg></div>

<section class="intro abs" role="img" aria-label="Faded background photo of a boardroom meeting"></section>

<div class="invite abs">
  <h2>MEMBERSHIP IS BY INVITATION ONLY FOR THOSE WHO:</h2>
  <div class="row">
    <span class="tick"><svg width="20" height="20" viewBox="0 0 20 20"><circle cx="10" cy="10" r="8.5" stroke="#fff" stroke-width="1.8" fill="none"/><path d="M6 10l3 3 5-6" stroke="#fff" stroke-width="1.8" fill="none"/></svg>Open to being challenged</span><span>|</span>
    <span class="tick"><svg width="20" height="20" viewBox="0 0 20 20"><circle cx="10" cy="10" r="8.5" stroke="#fff" stroke-width="1.8" fill="none"/><path d="M6 10l3 3 5-6" stroke="#fff" stroke-width="1.8" fill="none"/></svg>Commit to double-digit growth</span>
  </div>
  <div class="row">
    <span class="tick"><svg width="20" height="20" viewBox="0 0 20 20"><circle cx="10" cy="10" r="8.5" stroke="#fff" stroke-width="1.8" fill="none"/><path d="M6 10l3 3 5-6" stroke="#fff" stroke-width="1.8" fill="none"/></svg>Ongoing learning</span><span>|</span>
    <span class="tick"><svg width="20" height="20" viewBox="0 0 20 20"><circle cx="10" cy="10" r="8.5" stroke="#fff" stroke-width="1.8" fill="none"/><path d="M6 10l3 3 5-6" stroke="#fff" stroke-width="1.8" fill="none"/></svg>Giving &amp; receiving honest feedback</span>
  </div>
</div>

<div class="intro-lines abs">
  <p>If you are lonely with no one you can trust to talk<br>through tough decisions</p>
  <p>If you don’t have the right people in the right seats</p>
  <p>If you seek financial independence, professional and personal growth,<br>and avoiding burnout; our group might be right for you.</p>
</div>

<div class="awards abs">
  <h3>Our best-in-class members have received<br>the following awards:</h3>
  <p class="lead">After many years in the business world as the founder/CEO of six for-profit and five not-for-profit corporations, I understand the huge responsibility you have for making the right decisions for your company, the personal well-being of your employees and yourself.</p>
  <ul>
    <li>National Entrepreneur of the Year Finalists</li>
    <li>Regional Fastest Growing 500 and 5000 and Most Admired CEO Finalists</li>
    <li>Founders Monthly Top Company Cultures</li>
    <li class="wrap">Coastal Business Review’s Fastest Growing 100: Most Admired CEO, Most Admired Family Businesses, Healthiest Companies, Best Place to Work and Military Entrepreneurs Award Winners</li>
  </ul>
  <span class="btn">Learn more us</span>
</div>
<div class="photo-frame abs"></div>
<div class="photo-meeting abs" role="img" aria-label="Photo of a group leader presenting to members around a boardroom table"></div>

<div class="quote-card abs"></div>
<div class="portrait abs" role="img" aria-label="Portrait photo of member"></div>
<div class="arrows abs">
  <span><svg width="12" height="10" viewBox="0 0 12 10"><path d="M11 5H2M5 1L1 5l4 4" stroke="#fff" stroke-width="1.6" fill="none"/></svg></span>
  <span><svg width="12" height="10" viewBox="0 0 12 10"><path d="M1 5h9M7 1l4 4-4 4" stroke="#fff" stroke-width="1.6" fill="none"/></svg></span>
</div>
<div class="quote-mark abs">“</div>
<div class="quote-who abs"><b>Warren Delacroix,</b><br>President, The Halvorsen<br>Group</div>
<div class="quote-rule abs"></div>
<p class="quote-body abs">“I sold my company for $61.5M and the second three years later for $176M. Considering a 6-year investment of about $86,000 the ROI is considerable. While that is substantial, I found the consistent executive leadership training, employee practices, directions, and adjacent CEO council the most significant. This proved instrumental in managing the high growth and preparing the staff and company towards embracing.</p>

<div class="say abs">
  <div class="eyebrow">WHAT OUR MEMBERS SAY</div>
  <h2>ABOUT SUMMITRY GROUP</h2>
  <p>“The guidance I got. The people I met. The wisdom they brought. Without it, I wouldn’t have been able to success-fully sell my company for $50 million dollars. Based on my $75,000 membership, I received a 40,000 to 1 ROI. At the center of it is Derek who not only brought together a brilliant group of people but makes sure we all get what we need from each other. Drawing on a ton of personal experience, he’s a huge asset to any entrepreneur.”</p>
  <div class="name">Nolan Pierce</div>
  <div class="role">CEO, Brightline Audio</div>
  <span class="btn">Read 100+ testimonials</span>
</div>

<section class="blog-band abs"></section>
<div class="blog-head abs">
  <div class="eyebrow">DEREK’S BLOG</div>
  <h2>LATEDT NEWS AND UPDATES</h2>
</div>

<article class="card abs" style="left:112px">
  <div class="thumb" role="img" aria-label="Photo of members in discussion at a table" style="background:linear-gradient(160deg,#b9b6ae,#5d5a55)"><span class="date">Jan 07, 2022</span></div>
  <h3>What are OKRs and how<br>your team should adopt them</h3>
  <a>Learn More &gt;</a>
</article>
<article class="card abs" style="left:443px">
  <div class="thumb" role="img" aria-label="Group photo of peer CEOs in front of a colourful wall" style="background:linear-gradient(160deg,#6f8f86,#3d4a52)"><span class="date">Jan 07, 2022</span></div>
  <h3>Impressive peer CEOs<br>join a diverse blend of 17</h3>
  <a>Learn More &gt;</a>
</article>
<article class="card abs" style="left:775px">
  <div class="thumb" role="img" aria-label="Graphic showing member companies growth of 4.6 percent" style="background:linear-gradient(180deg,#f6d21b,#f48a1c 55%,#e8441c)"><span class="date">Jan 07, 2022</span></div>
  <h3>Proven Summitry methodology<br>according to Carrow Analytics,</h3>
  <a>Learn More &gt;</a>
</article>

<span class="btn more-news abs">Read more news</span>

<footer class="site-footer abs"></footer>
<div class="f-brand abs">
  <div class="brand-row"><span class="brand-mark"></span><span class="brand-name">Summitry</span></div>
  <div class="brand-tag">Peer councils for company<br>leaders and founders.</div>
</div>
<div class="f-vline abs" style="left:356px"></div>
<div class="f-col abs" style="left:389px">
  <h4>Contact Us</h4>
  <div class="item"><svg width="14" height="12" viewBox="0 0 14 12"><path d="M0 2l4-2 5 2 5-2v10l-5 2-5-2-4 2z" fill="#fff"/></svg><span>: 2210 Larkspur Avenue,<br>&nbsp;&nbsp;Dayton, Ohio, 45402.</span></div>
  <div class="item"><svg width="12" height="12" viewBox="0 0 12 12"><path d="M2 0l3 3-1.5 2a7 7 0 003.5 3.5L9 7l3 3-2 2C5 12 0 7 0 2z" fill="#fff"/></svg><span>: 555-014-2283</span></div>
  <div class="item"><svg width="13" height="10" viewBox="0 0 13 10"><rect width="13" height="10" rx="1" fill="#fff"/><path d="M1 1l5.5 4.5L12 1" stroke="#0f2c4c" fill="none"/></svg><span>: Derek @ DerekMulvane.com</span></div>
</div>
<div class="f-vline abs" style="left:676px"></div>
<div class="f-col abs" style="left:717px">
  <h4>Useful Links</h4>
  <div class="link">About The Group</div>
  <div class="link">Member Video Testimonials</div>
  <div class="link">Testimonials</div>
  <div class="link">Success Stories</div>
  <div class="link">Derek's Blog</div>
  <div class="link">Derek Mulvane Bio</div>
</div>
<div class="f-vline abs" style="left:949px"></div>
<div class="f-col abs" style="left:991px">
  <h4>Social</h4>
  <div class="f-social"><span></span><span></span><span></span></div>
</div>
<div class="f-rule abs"></div>
<div class="copyright abs">2022 © Summitry. All rights reserved.</div>
<div class="code abs">C24</div>

</body>
</html>
```